Irrigation Business needs their business cards modernised and revamped

I would like to keep my current logo, colours and revamp the format of the card.

I would like the card to be clean yet important.

Im not sure if you include texture but i would like the named logo to be indented into the card etc.

show me something alive and free something thats clinical to the point yet has a feel of achievement. i would like people to go nice card.

Target Market(s)

high end clients, corporate, sports field manger, the guys that make the decisions

Industry/Entity Type

Business

Contact Information for Business Card

nformation to be included

Dean Harlow (Director)
0487305526
dean@kolvat.biz
www.kestonfieldworks.com

instagram logo
google logo
facebook logo

Colors

Designer to choose colors to be used in the design.

Requirements
Nice to have
• indentations a really nice feel to the card good texture

```html
<!DOCTYPE html>
<html lang="en">
<head>
<meta charset="utf-8">
<title>Keston Fieldworks – Business Card</title>
<link href="https://fonts.googleapis.com/css2?family=Roboto+Condensed:wght@500;700&family=Open+Sans:wght@400;600&display=swap" rel="stylesheet">
<style>
  :root {
    --backdrop: #2a2a2a;
    --card-white: #f3f3f3;
    --brand-blue: #2f63a6;
    --card-blue: #3a6eab;
    --brand-green: #2f9e58;
    --text-grey: #4d4d4d;
    --faint-blue: #dde7ef;
    --white: #ffffff;
  }
  * { margin: 0; padding: 0; box-sizing: border-box; }
  html, body {
    width: 1200px; height: 960px; overflow: hidden;
    background: var(--backdrop);
  }
  .canvas { position: relative; width: 1200px; height: 960px; }

  .card {
    position: absolute; width: 600px; height: 343px; overflow: hidden;
  }
  .card-front { left: 314px; top: 113px; background: var(--card-white); }
  .card-back { left: 311px; top: 472px; background: var(--card-blue); }

  .front-emblem-faint {
    position: absolute; left: -40px; top: 0; width: 336px; height: 336px;
    border-radius: 50%; border: 26px solid var(--faint-blue); opacity: .8;
  }
  .name-marker {
    position: absolute; left: 0; top: 125px; width: 14px; height: 43px;
    background: var(--brand-blue);
  }
  .holder-name {
    position: absolute; left: 41px; top: 124px;
    font: 700 22px/1 "Roboto Condensed", sans-serif; color: var(--brand-blue);
    text-transform: uppercase;
  }
  .holder-role {
    position: absolute; left: 42px; top: 152px;
    font: 500 15px/1 "Roboto Condensed", sans-serif; color: var(--brand-green);
    letter-spacing: .5px; text-transform: uppercase;
  }
  .front-rule {
    position: absolute; left: 41px; top: 175px; width: 516px; height: 1.5px;
    background: var(--brand-blue);
  }
  .brand-front {
    position: absolute; right: 42px; top: 30px;
    display: flex; flex-direction: column; align-items: center; gap: 14px;
  }
  .brand-circle {
    width: 80px; height: 80px; border-radius: 50%; background: var(--brand-blue);
  }
  .brand-name {
    font: 700 25px/1 "Roboto Condensed", sans-serif; color: var(--brand-blue);
    text-transform: uppercase; letter-spacing: .3px;
  }
  .contact-list {
    position: absolute; left: 41px; top: 254px; list-style: none;
    font: 400 14px/19.5px "Open Sans", sans-serif; color: var(--text-grey);
  }
  .contact-list li { display: flex; align-items: center; gap: 8px; }
  .contact-list svg { width: 14px; height: 14px; fill: var(--brand-blue); }

  .brand-back {
    position: absolute; left: 203px; top: 71px; width: 194px; height: 194px;
    border-radius: 50%; border: 8px solid var(--white);
    display: flex; align-items: center; justify-content: center; text-align: center;
    font: 700 26px/1.1 "Roboto Condensed", sans-serif; color: var(--white);
    text-transform: uppercase;
  }
  .social-row {
    position: absolute; left: 60px; top: 290px; width: 480px; height: 28px;
    display: flex; align-items: center; justify-content: center; gap: 6px;
  }
  .social-row .rule {
    flex: 1; height: 1px;
    background: linear-gradient(90deg, transparent, rgba(255,255,255,.55));
  }
  .social-row .rule.end { background: linear-gradient(90deg, rgba(255,255,255,.55), transparent); }
  .social-dot { width: 26px; height: 26px; border-radius: 50%; background: var(--white); }
</style>
</head>
<body>
<main class="canvas">

  <section class="card card-front" aria-label="Business card front">
    <div class="front-emblem-faint"></div>
    <div class="name-marker"></div>
    <h1 class="holder-name">Dean Harlow</h1>
    <p class="holder-role">Director</p>
    <div class="front-rule"></div>

    <div class="brand-front">
      <div class="brand-circle"></div>
      <div class="brand-name">Keston Fieldworks</div>
    </div>

    <ul class="contact-list">
      <li>
        <svg viewBox="0 0 24 24" aria-hidden="true"><path d="M6.6 10.8a15 15 0 0 0 6.6 6.6l2.2-2.2a1 1 0 0 1 1-.25 11.4 11.4 0 0 0 3.6.57 1 1 0 0 1 1 1V20a1 1 0 0 1-1 1A17 17 0 0 1 3 4a1 1 0 0 1 1-1h3.5a1 1 0 0 1 1 1c0 1.25.2 2.45.57 3.57a1 1 0 0 1-.25 1z"/></svg>
        0487305526
      </li>
      <li>
        <svg viewBox="0 0 24 24" aria-hidden="true"><path d="M2 5h20v14H2z M3.5 6.5 12 13l8.5-6.5" fill="none" stroke="#2f63a6" stroke-width="2.2"/></svg>
        dean@kolvat.biz
      </li>
      <li>
        <svg viewBox="0 0 24 24" aria-hidden="true"><circle cx="12" cy="12" r="10"/><path d="M2 12h20M12 2c3 3 3 17 0 20M12 2c-3 3-3 17 0 20" fill="none" stroke="#f3f3f3" stroke-width="1.5"/></svg>
        www.kestonfieldworks.com
      </li>
    </ul>
  </section>

  <section class="card card-back" aria-label="Business card back">
    <div class="brand-back">Keston<br>Fieldworks</div>
    <div class="social-row">
      <span class="rule"></span>
      <span class="social-dot"></span>
      <span class="social-dot"></span>
      <span class="social-dot"></span>
      <span class="rule end"></span>
    </div>
  </section>

</main>
</body>
</html>
```